Looking for someone to design a business card for my plumbing business Quandor Plumbing Solutions I want the background also to be black, must attract clients. If possible I want the front to be the logo and the back to show maybe the details.

Target Market(s)

Clients

Industry/Entity Type

Plumbing maintenance

Contact Information for Business Card

Name: Felix, Contact: 0461 539 207, Email: quandorplumbingsolutions@mailbrook.example, Licence number 728093K

Font styles to use
Other font styles liked:
• as per logo maybe?

Colors

Designer to choose colors to be used in the design.

Requirements
Nice to have
• stating the service I provide, emergency plumbing, plumbing maintenance, drainage maintenance, block sewer and stormwater, camera and locating.

```html
<!DOCTYPE html>
<html lang="en">
<head>
<meta charset="utf-8">
<title>Quandor Plumbing Solutions – Business Card</title>
<link rel="stylesheet" href="https://fonts.googleapis.com/css2?family=Montserrat:wght@400;500;700;800&display=swap">
<style>
  :root {
    --stage: #3a3a3a;
    --card: #1f1f20;
    --blue: #4a90d9;
    --white: #ffffff;
  }
  * { box-sizing: border-box; margin: 0; padding: 0; }
  html, body { width: 1200px; height: 875px; overflow: hidden; }
  body {
    background: var(--stage);
    font-family: "Montserrat", Arial, sans-serif;
    position: relative;
  }
  .card {
    position: absolute;
    left: 290px;
    width: 620px;
    height: 354px;
    background: var(--card);
    border-radius: 22px;
    overflow: hidden;
    box-shadow: 0 14px 30px rgba(0,0,0,.45);
  }
  .card--front { top: 60px; }
  .card--back { top: 461px; }

  .brand {
    display: flex;
    align-items: center;
    gap: 12px;
    color: var(--blue);
    font-weight: 800;
    text-transform: uppercase;
    line-height: 1;
    white-space: nowrap;
  }
  .brand__dot {
    width: 14px; height: 14px; border-radius: 50%;
    background: var(--blue); flex: none;
  }

  /* Front */
  .card--front .brand {
    position: absolute; top: 120px; left: 0; right: 0;
    justify-content: center; font-size: 26px; letter-spacing: .5px;
  }
  .services {
    position: absolute; left: 0; right: 0; top: 204px;
    text-align: center; color: var(--white);
    font-size: 15px; font-weight: 500; line-height: 1.75;
  }
  .services .sep { color: var(--blue); margin: 0 8px; }

  /* Back */
  .card--back .brand {
    position: absolute; top: 48px; right: 44px;
    font-size: 19px; gap: 9px;
  }
  .card--back .brand__dot { width: 11px; height: 11px; }
  .rule-art { position: absolute; top: 0; left: 0; }
  .licence {
    position: absolute; top: 150px; right: 0;
    width: 250px; height: 30px;
    display: flex; align-items: center; justify-content: center;
    color: var(--white); font-size: 15px; font-weight: 500;
  }
  .person { position: absolute; left: 52px; top: 172px; }
  .person__name {
    color: var(--blue); font-size: 26px; font-weight: 800;
    text-transform: uppercase; letter-spacing: 1px; line-height: 1;
  }
  .person__role {
    color: var(--white); font-size: 15px; font-weight: 500;
    margin-top: 4px; line-height: 1.2;
  }
  .contacts {
    position: absolute; left: 52px; top: 262px;
    list-style: none; color: var(--white);
    font-size: 14px; font-weight: 500;
  }
  .contacts li { display: flex; align-items: center; gap: 10px; height: 24px; }
  .contacts svg { width: 13px; height: 13px; flex: none; }
  .social-dot {
    width: 13px; height: 13px; border-radius: 50%;
    background: var(--blue); flex: none;
  }
</style>
</head>
<body>

<section class="card card--front" aria-label="Business card front">
  <div class="brand">
    <span class="brand__dot"></span>
    <span class="brand__name">Quandor Plumbing Solutions</span>
  </div>
  <p class="services">
    Emergency plumbing<span class="sep">•</span>Plumbing maintenance<span class="sep">•</span>Drainage maintenance<br>
    Block sewer and stormwater<span class="sep">•</span>Camera and locating
  </p>
</section>

<section class="card card--back" aria-label="Business card back">
  <div class="brand">
    <span class="brand__dot"></span>
    <span class="brand__name">Quandor Plumbing Solutions</span>
  </div>

  <svg class="rule-art" width="620" height="354" viewBox="0 0 620 354" aria-hidden="true">
    <polygon points="370,150 620,150 620,180 384,180" fill="var(--blue)"/>
    <line x1="52" y1="250" x2="384" y2="180" stroke="var(--blue)" stroke-width="1.5"/>
  </svg>
  <div class="licence">Licence number 728093K</div>

  <div class="person">
    <p class="person__name">Felix</p>
    <p class="person__role">Founder &amp; CEO</p>
  </div>

  <ul class="contacts">
    <li>
      <svg viewBox="0 0 24 24" aria-hidden="true"><path fill="var(--blue)" d="M6.6 10.8a15.1 15.1 0 0 0 6.6 6.6l2.2-2.2a1 1 0 0 1 1-.25 11.4 11.4 0 0 0 3.6.57 1 1 0 0 1 1 1V20a1 1 0 0 1-1 1A17 17 0 0 1 3 4a1 1 0 0 1 1-1h3.5a1 1 0 0 1 1 1c0 1.25.2 2.45.57 3.6a1 1 0 0 1-.25 1z"/></svg>
      <span>0461 539 207</span>
    </li>
    <li>
      <svg viewBox="0 0 24 24" aria-hidden="true"><rect x="2" y="5" width="20" height="14" rx="2" fill="var(--blue)"/><path d="M3 6l9 7 9-7" fill="none" stroke="var(--card)" stroke-width="2"/></svg>
      <span>quandorplumbingsolutions@mailbrook.example</span>
    </li>
    <li>
      <span class="social-dot"></span>
      <span>@QuandorPlumbingSolutions</span>
    </li>
  </ul>
</section>

</body>
</html>
```